Walk Beside The River

Business Card design

Target Market(s)

People who require support in the commnity

Industry/Entity Type

Mental Health Support

Contact Information for Business Card

Mental Health Support Rosalind Tavener walkbesidetheriver@mailcove.com.au 0481 637 092 PO Box 926 Tallowood QLD 4599

Colors
6B429C
8869AF
B7A5CE
E3DAEB
F3F0F8

Requirements
Must have
• Logo & details listed above
Should not have
• No red or orange

```html
<!DOCTYPE html>
<html lang="en">
<head>
<meta charset="utf-8">
<title>Walk Beside The River — Business Card</title>
<link rel="stylesheet" href="https://fonts.googleapis.com/css2?family=Open+Sans:wght@400;600&display=swap">
<style>
  :root {
    --stage: #e6e3ea;
    --card-front: #fdfcf1;
    --card-back: #222128;
    --brand-purple: #6b429c;
    --accent-yellow: #efe630;
    --ink: #111111;
    --light-ink: #fdfcf1;
  }
  * { box-sizing: border-box; margin: 0; padding: 0; }
  html, body {
    width: 1200px; height: 780px; overflow: hidden;
    background: var(--stage);
    font-family: "Open Sans", Arial, sans-serif;
  }
  .canvas {
    width: 1200px; height: 780px;
    display: flex; align-items: center; justify-content: center; gap: 30px;
  }
  .card {
    width: 560px; height: 340px; position: relative; overflow: hidden;
    box-shadow: 0 10px 30px rgba(0,0,0,0.18);
  }
  .card--front { background: var(--card-front); }
  .card--back { background: var(--card-back); }

  .brand {
    position: absolute; display: flex; align-items: center; gap: 14px;
  }
  .brand__dot {
    width: 96px; height: 96px; border-radius: 50%;
    background: var(--brand-purple); flex: none;
  }
  .brand__name {
    font-weight: 600; font-size: 17px; letter-spacing: 0.04em;
    width: 130px; line-height: 1.3;
  }
  .card--front .brand { left: 34px; top: 30px; }
  .card--front .brand__name { color: var(--brand-purple); }
  .card--back .brand { right: 40px; top: 50%; transform: translateY(-50%); flex-direction: row-reverse; }
  .card--back .brand__name { color: var(--light-ink); text-align: right; }

  .details {
    position: absolute; left: 40px; bottom: 28px; right: 24px;
    color: var(--ink); font-size: 16px; line-height: 1.32;
  }
  .details__role, .details__name { display: block; }
  .details__name { margin-bottom: 4px; }
  .contact { list-style: none; }
  .contact__item { display: flex; align-items: center; gap: 10px; white-space: nowrap; }
  .contact__icon { width: 15px; height: 15px; flex: none; }
</style>
</head>
<body>
<main class="canvas">
  <section class="card card--front" aria-label="Card front">
    <div class="brand">
      <span class="brand__dot"></span>
      <span class="brand__name">Walk Beside The River</span>
    </div>
    <div class="details">
      <span class="details__role">Mental Health Support</span>
      <span class="details__name">Rosalind Tavener</span>
      <ul class="contact">
        <li class="contact__item">
          <svg class="contact__icon" viewBox="0 0 16 16" aria-hidden="true"><path d="M4 1.5l2.5 3-1.5 1.5c.8 2 2.5 3.7 4.5 4.5L11 9l3 2.5-1.5 2.5C7 14 2 9 2 3z" fill="var(--accent-yellow)"/></svg>
          <span>0481 637 092</span>
        </li>
        <li class="contact__item">
          <svg class="contact__icon" viewBox="0 0 16 16" aria-hidden="true"><rect x="1.5" y="3.5" width="13" height="9" rx="1" fill="none" stroke="var(--accent-yellow)" stroke-width="1.6"/><path d="M2 4.5l6 4.5 6-4.5" fill="none" stroke="var(--accent-yellow)" stroke-width="1.6"/></svg>
          <span>walkbesidetheriver@mailcove.com.au</span>
        </li>
        <li class="contact__item">
          <svg class="contact__icon" viewBox="0 0 16 16" aria-hidden="true"><path d="M8 1a5 5 0 0 1 5 5c0 3.5-5 9-5 9S3 9.5 3 6a5 5 0 0 1 5-5z" fill="var(--accent-yellow)"/><circle cx="8" cy="6" r="1.8" fill="var(--card-front)"/></svg>
          <span>PO Box 926 Tallowood QLD 4599</span>
        </li>
      </ul>
    </div>
  </section>

  <section class="card card--back" aria-label="Card back">
    <div class="brand">
      <span class="brand__dot"></span>
      <span class="brand__name">Walk Beside The River</span>
    </div>
  </section>
</main>
</body>
</html>
```